Business card design for holistic health care clinic

We need a double-sided business card design for our holistic health care clinic that integrates our logo design and also its color scheme. My business is called Valmira. It is an integrative medicine clinic. You have already done the logo for me. Please ensure an elegant and upscale design that is not cluttered, but still has all the necessary information (please see below for details).

Target Market(s)

Wellness, fitness, rehabilitation for educated, well-traveled open-minded clients who are focused on natural, organic, balanced and preventive healthcare and lifestyle.

Industry/Entity Type

Medical

Contact Information for Business Card

Modern, clean.

Number of Pages Required

1 page

Font styles to use
Serif
Sans Serif

Colors

Designer to choose colors to be used in the design.

Requirements
Must have
• Logo on one side, all other information on the other side.
• Other information should include:
• Tobias Wrenfeld - DOE, CPT, LMT
• 4100 East Marrow Drive
• Austin, TX 78119
• 512 555 0148
• 818 555 0192
• info@ValmiraHealth.example
• t.wrenfeld@ValmiraHealth.example
Nice to have
• Darker background on front - but not totally black - shaded/dark gray.

```html
<!DOCTYPE html>
<html lang="en">
<head>
<meta charset="utf-8">
<title>Valmira – Business Card</title>
<link href="https://fonts.googleapis.com/css2?family=Nunito:wght@700;800&family=Roboto+Condensed:ital,wght@0,700;1,300&family=Roboto:wght@400&display=swap" rel="stylesheet">
<style>
  :root {
    --stage: #2a2a2b;
    --card-light: #f4f4f4;
    --card-dark: #2e2e30;
    --brand-blue: #1a93d2;
    --text-light: #f2f2f2;
    --text-muted: #555555;
    --rule: #8a8a8a;
    --white: #ffffff;
  }
  * { margin: 0; padding: 0; box-sizing: border-box; }
  html, body { width: 1200px; height: 960px; overflow: hidden; }
  body { background: var(--stage); position: relative; font-family: "Roboto", Arial, sans-serif; }

  .card {
    position: absolute;
    left: 320px;
    width: 600px;
    border-radius: 18px;
    overflow: hidden;
  }
  .card-front { top: 95px; height: 355px; background: var(--card-light); }
  .card-back { top: 493px; height: 342px; background: var(--card-dark); }

  /* Front */
  .brand {
    position: absolute; left: 0; right: 0; top: 150px;
    text-align: center; color: var(--brand-blue);
    font-family: "Nunito", Arial, sans-serif;
  }
  .brand-name { font-weight: 800; font-size: 66px; line-height: 66px; letter-spacing: 1px; text-transform: uppercase; }
  .brand-sub { font-weight: 800; font-size: 19px; line-height: 24px; margin-top: 2px; }
  .brand-dot {
    display: inline-block; width: 14px; height: 14px; border-radius: 50%;
    background: var(--brand-blue); vertical-align: middle; margin-right: 10px; position: relative; top: -6px;
  }
  .tagline {
    position: absolute; left: 0; right: 0; top: 284px;
    display: flex; align-items: center; justify-content: center; gap: 8px;
    font-family: "Roboto Condensed", Arial, sans-serif; font-style: italic; font-weight: 300;
    font-size: 18px; color: var(--text-muted);
  }
  .tagline-rule { width: 100px; height: 1px; background: var(--rule); }

  /* Back */
  .corner-swoosh { position: absolute; right: 0; top: 0; }
  .holder {
    position: absolute; left: 33px; top: 31px;
    font-family: "Roboto Condensed", Arial, sans-serif; font-weight: 700;
    color: var(--brand-blue); text-transform: uppercase;
  }
  .holder-name { font-size: 22px; }
  .holder-titles { font-size: 13px; }
  .address {
    position: absolute; left: 33px; top: 69px;
    color: var(--text-light); font-size: 14.5px; line-height: 18px;
  }
  .contacts { position: absolute; left: 33px; top: 116px; list-style: none; }
  .contacts li {
    display: flex; align-items: center; gap: 8px;
    color: var(--text-light); font-size: 14.5px; line-height: 19px;
  }
  .contacts svg { width: 14px; height: 14px; fill: var(--brand-blue); flex: none; }
  .back-brand {
    position: absolute; left: 33px; top: 252px;
    color: var(--brand-blue); font-family: "Nunito", Arial, sans-serif; text-align: center;
  }
  .back-brand .brand-name { font-size: 44px; line-height: 46px; }
  .back-brand .brand-sub { font-size: 13px; line-height: 16px; margin-top: 0; }
</style>
</head>
<body>

<section class="card card-front" aria-label="Card front">
  <div class="brand">
    <div class="brand-name"><span class="brand-dot"></span>Valmira</div>
    <div class="brand-sub">Integrative Holistic Medicine</div>
  </div>
  <div class="tagline">
    <span class="tagline-rule"></span>
    <span>helping the body help itself</span>
    <span class="tagline-rule"></span>
  </div>
</section>

<section class="card card-back" aria-label="Card back">
  <svg class="corner-swoosh" width="600" height="342" viewBox="0 0 600 342">
    <path d="M232 342 C420 305 560 200 552 0 L600 0 L600 342 Z" fill="var(--white)"/>
  </svg>

  <div class="holder">
    <span class="holder-name">Tobias Wrenfeld</span>
    <span class="holder-titles"> - DOE, CPT, LMT</span>
  </div>

  <address class="address" style="font-style: normal;">
    4100 East Marrow Drive<br>
    Austin, TX 78119
  </address>

  <ul class="contacts">
    <li>
      <svg viewBox="0 0 24 24"><path d="M6.6 10.8a15.1 15.1 0 0 0 6.6 6.6l2.2-2.2c.3-.3.7-.4 1-.2 1.1.4 2.3.6 3.6.6.6 0 1 .4 1 1V20c0 .6-.4 1-1 1A17 17 0 0 1 3 4c0-.6.4-1 1-1h3.5c.6 0 1 .4 1 1 0 1.3.2 2.5.6 3.6.1.3 0 .7-.2 1z"/></svg>
      512 555 0148
    </li>
    <li>
      <svg viewBox="0 0 24 24"><path d="M7 1h10a2 2 0 0 1 2 2v18a2 2 0 0 1-2 2H7a2 2 0 0 1-2-2V3a2 2 0 0 1 2-2zm0 3v14h10V4zm5 15.5a1 1 0 1 0 0 2 1 1 0 0 0 0-2z"/></svg>
      818 555 0192
    </li>
    <li>
      <svg viewBox="0 0 24 24"><path d="M2 5h20v14H2zm2 2v.4l8 5.2 8-5.2V7z"/></svg>
      t.wrenfeld@ValmiraHealth.example
    </li>
    <li>
      <svg viewBox="0 0 24 24"><path d="M12 2a10 10 0 1 0 0 20 10 10 0 0 0 0-20zm-1 17.9A8 8 0 0 1 4.1 10L9 15v1a2 2 0 0 0 2 2zm6.9-2.5A2 2 0 0 0 16 16h-1v-3a1 1 0 0 0-1-1H8v-2h2a1 1 0 0 0 1-1V7h2a2 2 0 0 0 2-2v-.4a8 8 0 0 1 2.9 12.8z"/></svg>
      www.ValmiraHealth.example
    </li>
  </ul>

  <div class="back-brand">
    <div class="brand-name" style="font-weight:800;text-transform:uppercase;letter-spacing:1px;">Valmira</div>
    <div class="brand-sub" style="font-weight:800;">Integrative Holistic Medicine</div>
  </div>
</section>

</body>
</html>
```